real esate business card with company logo and name

we need a business card design for a real esate company

The company name is Walsh & Brand Pty Ltd, and we have our logo designed and will upload. We want classic or moden feel. Black or white background. looks more textured. Should include folowinginformations
Owen Walsh and Lucy Brand
Sales Agents & Onsite Manager
p: 07 5948 2063
F: 07 5948 2174
M:0431 857 219
3/42 Marlow Crescent, FERNLEA QLD 4213

We want this business card looks professonal. Thank you in advance.

Industry/Entity Type

Real Estate Agent

Contact Information for Business Card

Owen Walsh and Lucy Brand
Onsite Manager & Sales Agents
p: 07 5948 2063
M:0431 857 219

Font styles to use
Serif

Colors
000000
fbfbfb
333333
959595

Requirements
Must have
• company logo and name, black or white back ground

```html
<!DOCTYPE html>
<html lang="en">
<head>
<meta charset="utf-8">
<title>Walsh &amp; Brand Pty Ltd – Business Card</title>
<link rel="stylesheet" href="https://fonts.googleapis.com/css2?family=Open+Sans:wght@400;600&display=swap">
<style>
  :root {
    --ink: #000000;
    --paper: #fbfbfb;
    --charcoal: #333333;
    --steel: #959595;
    --backdrop: #e4e4e4;
    --divider: #d4d4d4;
  }
  * { box-sizing: border-box; margin: 0; padding: 0; }
  html, body {
    width: 1200px; height: 892px; overflow: hidden;
    background: var(--backdrop);
    font-family: "Open Sans", Arial, sans-serif;
  }
  .card {
    position: absolute; left: 120px; top: 153px;
    width: 960px; height: 586px;
    background: linear-gradient(160deg, #ffffff 0%, var(--paper) 55%, #ececec 100%);
    box-shadow: 0 10px 30px rgba(0,0,0,.25);
    overflow: hidden;
  }
  .card__brand {
    position: absolute; left: 46px; top: 262px;
    display: flex; align-items: center; gap: 14px;
  }
  .card__brand-mark {
    width: 22px; height: 22px; background: var(--steel);
  }
  .card__brand-name {
    font-size: 22px; font-weight: 400; letter-spacing: 1.5px;
    color: var(--steel); text-transform: uppercase;
  }
  .card__divider {
    position: absolute; left: 0; right: 0; top: 318px; height: 14px;
    background: var(--divider);
    border-top: 2px solid #f4f4f4;
    border-bottom: 2px solid var(--steel);
  }
  .card__band {
    position: absolute; left: 0; right: 0; top: 332px; bottom: 0;
    background: radial-gradient(ellipse at 70% 20%, #1a1a1a 0%, var(--ink) 70%);
    color: var(--paper);
  }
  .card__names {
    position: absolute; left: 46px; top: 34px; width: 560px;
  }
  .card__holders {
    font-size: 42px; font-weight: 400; line-height: 1.1; letter-spacing: -0.5px;
    white-space: nowrap;
  }
  .card__role {
    margin-top: 8px; font-size: 25px; font-weight: 400; color: #e6e6e6;
    white-space: nowrap;
  }
  .card__contact {
    position: absolute; left: 636px; top: 28px;
    list-style: none; font-size: 22px; line-height: 1.5;
  }
  .card__contact li { display: flex; align-items: center; gap: 16px; white-space: nowrap; }
  .card__contact .indent { padding-left: 38px; }
  .icon { width: 22px; height: 22px; flex: none; }
</style>
</head>
<body>
  <div class="card">
    <div class="card__brand">
      <span class="card__brand-mark"></span>
      <span class="card__brand-name">Walsh &amp; Brand Pty Ltd.</span>
    </div>
    <div class="card__divider"></div>
    <div class="card__band">
      <div class="card__names">
        <p class="card__holders">Owen Walsh and Lucy Brand</p>
        <p class="card__role">Onsite Manager &amp; Sales Agents</p>
      </div>
      <ul class="card__contact">
        <li>
          <svg class="icon" viewBox="0 0 24 24" aria-hidden="true">
            <rect width="24" height="24" fill="#fbfbfb"/>
            <path d="M7 5c1 0 2 2 2.5 3s-1 1.5-1 2 2.5 4.5 4.5 5 1-1 2-1 3 1.5 3 2.5-1.5 2.5-3 2.5C10 19 5 14 5 8c0-1.5 1-3 2-3z" fill="#000"/>
          </svg>
          <span>07 5948 2063</span>
        </li>
        <li>
          <svg class="icon" viewBox="0 0 24 24" aria-hidden="true">
            <rect width="24" height="24" fill="#fbfbfb"/>
            <rect x="7" y="3" width="10" height="18" rx="1.5" fill="#000"/>
            <rect x="9" y="5.5" width="6" height="9" fill="#fbfbfb"/>
            <circle cx="12" cy="18" r="1.2" fill="#fbfbfb"/>
          </svg>
          <span>0431 857 219</span>
        </li>
        <li>
          <svg class="icon" viewBox="0 0 24 24" aria-hidden="true">
            <rect width="24" height="24" fill="#fbfbfb"/>
            <path d="M12 4 3.5 12H6v8h4.5v-5h3v5H18v-8h2.5z" fill="#000"/>
          </svg>
          <span>3/42 Marlow Crescent,</span>
        </li>
        <li class="indent"><span>FERNLEA QLD 4213</span></li>
      </ul>
    </div>
  </div>
</body>
</html>
```